Brindle Yard Care. The best in the biz

I run a lawn care service that offers full service mowing. 100% satisfaction guarantee. Fast, Friendly, quality service "I am your lawns best friend" I cut residential lawns. I offer a mow package that includes trimming, edging and clean up. Prices very from 20 dollars to 75. I want my logo to stand out. Free estimates

Target Market(s)

Home owners

Industry/Entity Type

Landscaping

Contact Information for Business Card

555-812-4473 tomvale48@quillmail.net Derek. Brindle Yard care

Colors
f37122
9bcb3c
cadf82

Requirements
Must have
• Company name.
• Phone number
• Email
• My services
• images
Nice to have
• A sun that is growing grass.
Should not have
• Incorrect information

```html
<!DOCTYPE html>
<html lang="en">
<head>
<meta charset="UTF-8">
<title>Brindle Yard Care — Business Card</title>
<link href="https://fonts.googleapis.com/css2?family=Open+Sans:wght@400;600;700&display=swap" rel="stylesheet">
<style>
  :root {
    --backdrop: #3b3431;
    --card-dark: #1f1f1f;
    --card-green: #9bcb3c;
    --accent-green: #9bcb3c;
    --mark-grey: #555555;
    --text-light: #e6e6e6;
    --white: #ffffff;
    --divider: #4a4a4a;
  }
  * { margin: 0; padding: 0; box-sizing: border-box; }
  html, body {
    width: 1200px; height: 844px; overflow: hidden;
    background: var(--backdrop);
    font-family: "Open Sans", Arial, sans-serif;
  }
  .stage {
    position: relative; width: 1200px; height: 844px;
    display: flex; align-items: center; justify-content: center; gap: 50px;
  }
  .card {
    position: relative; width: 525px; height: 300px;
    box-shadow: 0 10px 30px rgba(0,0,0,0.45);
  }

  /* Back: contact side */
  .card--contact { background: var(--card-dark); }
  .brand-block {
    position: absolute; left: 40px; top: 78px; width: 250px;
    display: flex; flex-direction: column; align-items: center;
  }
  .brand-dot {
    width: 74px; height: 74px; border-radius: 50%;
    background: var(--mark-grey); border: 3px solid var(--accent-green);
  }
  .brand-name {
    margin-top: 14px; color: var(--accent-green);
    font-size: 25px; font-weight: 400; white-space: nowrap;
  }
  .divider {
    position: absolute; left: 305px; top: 40px; width: 1px; height: 160px;
    background: var(--divider);
  }
  .contact {
    position: absolute; left: 325px; top: 48px; color: var(--text-light);
  }
  .contact-name {
    color: var(--accent-green); font-weight: 700; font-size: 16px; margin-bottom: 22px;
  }
  .contact-line {
    display: flex; align-items: center; gap: 8px;
    font-size: 13px; margin-bottom: 6px;
  }
  .contact-line svg { width: 11px; height: 11px; flex: none; }

  /* Front: service side */
  .card--services { background: var(--card-green); }
  .front-mark {
    position: absolute; left: 45px; top: 55px;
    width: 190px; height: 190px; border-radius: 50%;
    background: var(--mark-grey); border: 6px solid var(--white);
    display: flex; align-items: center; justify-content: center;
    text-align: center;
  }
  .front-mark-name {
    color: var(--white); font-size: 19px; font-weight: 600; line-height: 1.25;
  }
  .services {
    position: absolute; right: 30px; top: 100px;
    text-align: right; color: var(--white);
    font-weight: 600; font-size: 17px; line-height: 1.95;
  }
</style>
</head>
<body>
  <main class="stage">
    <section class="card card--contact">
      <div class="brand-block">
        <div class="brand-dot"></div>
        <div class="brand-name">Brindle Yard Care</div>
      </div>
      <div class="divider"></div>
      <div class="contact">
        <div class="contact-name">Derek</div>
        <div class="contact-line">
          <svg viewBox="0 0 24 24" aria-hidden="true"><path fill="#9bcb3c" d="M6.6 10.8a15.1 15.1 0 0 0 6.6 6.6l2.2-2.2a1 1 0 0 1 1-.25 11.4 11.4 0 0 0 3.6.6 1 1 0 0 1 1 1V20a1 1 0 0 1-1 1A17 17 0 0 1 3 4a1 1 0 0 1 1-1h3.5a1 1 0 0 1 1 1c0 1.25.2 2.45.6 3.6a1 1 0 0 1-.25 1z"/></svg>
          <span>555-812-4473</span>
        </div>
        <div class="contact-line">
          <svg viewBox="0 0 24 24" aria-hidden="true"><rect x="2" y="5" width="20" height="14" fill="#9bcb3c"/><path d="M2 5l10 8 10-8" fill="none" stroke="#1f1f1f" stroke-width="2"/></svg>
          <span>tomvale48@quillmail.net</span>
        </div>
      </div>
    </section>

    <section class="card card--services">
      <div class="front-mark">
        <div class="front-mark-name">Brindle<br>Yard Care</div>
      </div>
      <div class="services">
        <p>100% satisfaction guarantee.</p>
        <p>Fast, Friendly, Quality Service</p>
        <p>I am your lawns best friend</p>
      </div>
    </section>
  </main>
</body>
</html>
```